Professional BIO Template with photo and logo

Hello,
I need a professional Bio template developed via Microsoft WORD ASAP!!!!! I would like to just be able to add the text I need to add. So resize-able text boxes. Potentially able to adjust the font. These are the things I need added it to include.
Head shot (attached)
Text Box for Name
Text Box for phone number
Text box for email
KVT Logo (attached)
Maybe a blue banner at the top or some background boxes that are blue or grey. Here are the pantone colors that our company uses.

CORE COLOR
100c 91m 17y 6k 38r 58g 128b Hex #263A80 Pantone 7687 C

CORE CONTRAST COLOR
36c 29m 28y 0k 168r 168g 170b Hex #669999 Pantone Cool Gray 6C

I also attached some examples of what we have been looking at. Instead of green add the blue...instead of black maybe just be white.

Thank you

```html
<!DOCTYPE html>
<html lang="en">
<head>
<meta charset="utf-8">
<title>Daniel Reeves – Bio</title>
<link href="https://fonts.googleapis.com/css2?family=Mulish:wght@300;400;600;700;800;900&display=swap" rel="stylesheet">
<style>
  :root {
    --core-blue: #263A80;
    --header-blue: #2d4087;
    --teal: #5f9190;
    --paper: #ececec;
    --ink: #222428;
    --grey-line: #9a9a9a;
    --white: #ffffff;
  }
  * { margin: 0; padding: 0; box-sizing: border-box; }
  html, body { width: 947px; height: 1200px; overflow: hidden; }
  body { font-family: "Mulish", Arial, sans-serif; background: var(--paper); color: var(--ink); }
  .page { position: relative; width: 947px; height: 1200px; background: var(--paper); overflow: hidden; }

  .header { position: absolute; left: 0; top: 0; width: 947px; height: 350px; }
  .header-shapes { position: absolute; inset: 0; }

  .headshot {
    position: absolute; left: 101px; top: 41px; width: 322px; height: 342px;
    border-radius: 14px;
    background: linear-gradient(180deg, #f2f2f2 0%, #e6e6e6 55%, #1f2532 56%, #1a1f2b 100%);
  }

  .identity { position: absolute; left: 476px; top: 92px; color: var(--white); }
  .identity-name { font-size: 28px; font-weight: 900; letter-spacing: 0; line-height: 1; white-space: nowrap; }
  .identity-title { margin-top: 18px; font-size: 14.5px; font-weight: 600; }

  .contact {
    position: absolute; left: 476px; width: 182px; height: 36px;
    background: var(--teal); color: var(--white);
    display: flex; align-items: center; gap: 10px; padding-left: 10px;
    border-left: 3px solid var(--white);
  }
  .contact-phone { top: 169px; }
  .contact-email { top: 215px; }
  .contact-icon {
    width: 22px; height: 22px; border-radius: 50%; background: var(--core-blue);
    display: flex; align-items: center; justify-content: center; flex: none;
  }
  .contact-text { display: flex; flex-direction: column; }
  .contact-label { font-size: 9.5px; font-weight: 800; line-height: 1.2; }
  .contact-value { font-size: 9.5px; font-weight: 400; line-height: 1.2; }

  .brand-mark {
    position: absolute; left: 759px; top: 25px; width: 146px; height: 98px;
    border: 2px solid var(--white);
    display: flex; align-items: center; justify-content: center; gap: 8px;
    color: var(--white); font-size: 32px; font-weight: 800; letter-spacing: 2px;
  }
  .brand-square { width: 12px; height: 12px; background: var(--white); }

  .divider {
    position: absolute; left: 101px; top: 398px; width: 745px; height: 70px;
    display: flex; align-items: flex-start; gap: 14px;
  }
  .divider-side { position: relative; flex: 1; height: 70px; }
  .divider-letters {
    flex: none; margin-top: 12px;
    font-size: 76px; font-weight: 300; color: var(--grey-line); line-height: 1;
    letter-spacing: 4px; padding-left: 4px;
  }
  .rule { position: absolute; height: 5px; background: var(--grey-line); }
  .rule-long { left: 0; right: 0; top: 57px; }
  .divider-left .rule-short { left: 50%; right: 0; top: 36px; }
  .divider-right .rule-short { left: 0; right: 50%; top: 36px; }

  .about { position: absolute; left: 101px; top: 490px; width: 745px; }
  .about-heading { font-size: 28px; font-weight: 800; color: var(--ink); margin-bottom: 18px; }
  .about-text { font-size: 11.2px; line-height: 19.3px; margin-bottom: 14px; color: var(--ink); text-align: left; }

  .skyline {
    position: absolute; left: 0; top: 1042px; width: 947px; height: 85px;
    background: linear-gradient(180deg, rgba(154,154,154,0) 0%, rgba(154,154,154,0.25) 100%);
    border-bottom: 3px solid var(--grey-line);
  }

  .footer {
    position: absolute; left: 0; top: 1127px; width: 947px; height: 73px;
    background: var(--core-blue); color: var(--white);
    display: flex; align-items: center; justify-content: center;
    font-size: 12px; font-weight: 400;
  }
</style>
</head>
<body>
<main class="page">
  <header class="header">
    <svg class="header-shapes" width="947" height="350" viewBox="0 0 947 350">
      <rect x="0" y="0" width="947" height="350" fill="var(--header-blue)"/>
      <rect x="0" y="326" width="947" height="24" fill="var(--teal)"/>
      <path d="M0 210 Q18 210 18 230 L18 262 Q18 282 38 282 L110 282 L110 350 L0 350 Z" fill="var(--teal)"/>
      <path d="M947 210 Q929 210 929 230 L929 262 Q929 282 909 282 L880 282 Q860 282 860 302 L860 326 L947 326 Z" fill="var(--teal)"/>
      <rect x="121" y="25" width="319" height="340" rx="14" fill="var(--teal)"/>
    </svg>

    <div class="headshot" role="img" aria-label="Head shot portrait of Daniel Reeves in a dark blazer and white shirt"></div>

    <div class="identity">
      <h1 class="identity-name">DANIEL REEVES</h1>
      <p class="identity-title">Excepteur sint occaecat cupidatat</p>
    </div>

    <div class="contact contact-phone">
      <span class="contact-icon">
        <svg width="8" height="11" viewBox="0 0 8 11"><rect x="1" y="0.75" width="6" height="9.5" rx="1.2" fill="none" stroke="#fff" stroke-width="1.3"/><circle cx="4" cy="8.3" r="0.7" fill="#fff"/></svg>
      </span>
      <span class="contact-text">
        <span class="contact-label">Phone Number</span>
        <span class="contact-value">+1 555 0142 37810</span>
      </span>
    </div>

    <div class="contact contact-email">
      <span class="contact-icon">
        <svg width="11" height="8" viewBox="0 0 11 8"><rect x="0" y="0" width="11" height="8" rx="1" fill="#fff"/><path d="M0.5 0.8 L5.5 4.6 L10.5 0.8" fill="none" stroke="var(--core-blue)" stroke-width="1.1"/></svg>
      </span>
      <span class="contact-text">
        <span class="contact-label">Email</span>
        <span class="contact-value">info@danielreeves.com</span>
      </span>
    </div>

    <div class="brand-mark"><span class="brand-square"></span>KVT</div>
  </header>

  <div class="divider">
    <div class="divider-side divider-left">
      <span class="rule rule-short"></span>
      <span class="rule rule-long"></span>
    </div>
    <span class="divider-letters">KVT</span>
    <div class="divider-side divider-right">
      <span class="rule rule-short"></span>
      <span class="rule rule-long"></span>
    </div>
  </div>

  <section class="about">
    <h2 class="about-heading">About Daniel Reeves</h2>
    <p class="about-text">Sed ut perspiciatis unde omnis iste natus error sit voluptatem accusantium doloremque laudantium, totam rem aperiam, eaque ipsa quae ab illo inventore veritatis et quasi architecto beatae vitae dicta sunt explicabo. Nemo enim ipsam voluptatem quia voluptas sit aspernatur aut odit aut fugit, sed quia consequuntur magni dolores eos qui ratione voluptatem sequi nesciunt. Neque porro quisquam est, qui dolorem ipsum quia dolor sit amet, consectetur, adipisci velit, sed quia non numquam eius modi tempora incidunt ut labore et dolore magnam aliquam quaerat voluptatem. Ut enim ad minima veniam, quis nostrum exercitationem ullam corporis suscipit laboriosam, nisi ut aliquid ex ea commodi consequatur? Quis autem vel eum iure reprehenderit qui in ea voluptate velit esse quam nihil molestiae consequatur</p>
    <p class="about-text">Sed ut perspiciatis unde omnis iste natus error sit voluptatem accusantium doloremque laudantium, totam rem aperiam, eaque ipsa quae ab illo inventore veritatis et quasi architecto beatae vitae dicta sunt explicabo. Nemo enim ipsam voluptatem quia voluptas sit aspernatur aut odit aut fugit, sed quia consequuntur magni dolores eos qui ratione voluptatem sequi nesciunt. Neque porro quisquam est, qui dolorem ipsum quia dolor sit amet, consectetur, adipisci velit, sed quia non numquam eius modi tempora incidunt ut labore et dolore magnam aliquam quaerat voluptatem. Ut enim ad minima veniam, quis nostrum exercitationem ullam corporis suscipit laboriosam, nisi ut aliquid ex ea commodi consequatur? Quis autem vel eum iure reprehenderit qui in ea voluptate velit esse quam nihil molestiae consequatur</p>
    <p class="about-text">Sed ut perspiciatis unde omnis iste natus error sit voluptatem accusantium doloremque laudantium, totam rem aperiam, eaque ipsa quae ab illo inventore veritatis et quasi architecto beatae vitae dicta sunt explicabo. Nemo enim ipsam voluptatem quia voluptas sit aspernatur aut odit aut fugit, sed quia consequuntur magni dolores eos qui ratione voluptatem sequi nesciunt. Neque porro quisquam est, qui dolorem ipsum quia dolor sit amet, consectetur, adipisci velit, sed quia non numquam eius modi tempora incidunt ut labore et dolore magnam aliquam quaerat voluptatem. Ut enim ad minima veniam, quis nostrum exercitationem ullam corporis suscipit laboriosam, nisi ut aliquid ex ea commodi consequatur? Quis autem vel eum iure reprehenderit qui in ea voluptate velit esse quam nihil molestiae consequatur</p>
    <p class="about-text">Sed ut perspiciatis unde omnis iste natus error sit voluptatem accusantium doloremque laudantium, totam rem aperiam, eaque ipsa quae ab illo inventore veritatis et quasi architecto beatae vitae dicta sunt explicabo. Nemo enim ipsam voluptatem quia voluptas sit aspernatur aut odit aut fugit, sed quia consequuntur magni dolores eos qui ratione voluptatem sequi nesciunt. Neque porro quisquam est, qui dolorem ipsum quia dolor</p>
  </section>

  <div class="skyline" role="img" aria-label="Grey outline drawing of a repeating city skyline"></div>

  <footer class="footer">Copyright © 2022 KVT. All rights reserved.</footer>
</main>
</body>
</html>
```